Verodex business card

Business card for sustainable investment company called "Verodex". Verodex is an exchange platform selling carbon credits between buyers and sellers. Carbon Credits are an environmental commodity for reducing global carbon emissions.

the card should obviously have our logo and the theme should be sustainability/environment mixed with a trading platform.

Contact Information for Business Card

Logo, Name, Title, Phone, Email

Colors
0054AA
0677BA
7BADD7
CADEEF
E8F1F8
0094D4
00A9DD
6FCCEA
C7EBF8
E9F6FB
00AB8E
00BBA5
67D7C9
C6EFE9
E9F9F6
59FF00
82FF00
B8FF75
E3FFCB
F4FFEA

```html
<!DOCTYPE html>
<html lang="en">
<head>
<meta charset="utf-8">
<title>Verodex business card</title>
<link href="https://fonts.googleapis.com/css2?family=Montserrat:wght@600&family=Raleway:wght@300;400;600&display=swap" rel="stylesheet">
<style>
  :root {
    --canvas: #e9f6fb;
    --card-blue: #0054aa;
    --card-blue-deep: #004a96;
    --teal: #00bba5;
    --mint: #67d7c9;
    --lime: #82ff00;
    --lime-soft: #b8ff75;
    --sky: #6fccea;
    --text-white: #ffffff;
    --text-soft: #e9f6fb;
  }
  * { margin: 0; padding: 0; box-sizing: border-box; }
  html, body {
    width: 1200px; height: 977px; overflow: hidden;
    background: var(--canvas);
  }
  .stage { position: relative; width: 1200px; height: 977px; }
  .card {
    position: absolute;
    width: 580px; height: 340px;
    background: linear-gradient(160deg, var(--card-blue) 0%, var(--card-blue-deep) 100%);
    border-radius: 22px;
    overflow: hidden;
    box-shadow: 0 10px 28px rgba(0, 84, 170, 0.22);
  }
  .card-front { left: 90px; top: 100px; }
  .card-back { left: 530px; top: 540px; }

  .eco-band {
    position: absolute; left: 0; right: 0; bottom: 0; height: 10px;
    background: linear-gradient(90deg, var(--teal) 0%, var(--mint) 45%, var(--lime) 100%);
  }

  .brand-front {
    position: absolute; left: 0; right: 0; top: 0; bottom: 10px;
    display: flex; align-items: center; justify-content: center; gap: 22px;
  }
  .brand-dot {
    width: 34px; height: 34px; border-radius: 50%;
    background: var(--lime);
  }
  .brand-name {
    font-family: "Montserrat", sans-serif; font-weight: 600;
    font-size: 58px; letter-spacing: 2px; color: var(--text-white);
  }
  .brand-corner {
    position: absolute; right: 34px; top: 30px;
    font-family: "Montserrat", sans-serif; font-weight: 600;
    font-size: 18px; letter-spacing: 1.5px; color: var(--lime-soft);
  }

  .identity {
    position: absolute; left: 0; right: 0; top: 150px;
    display: flex; align-items: center; justify-content: center; gap: 22px;
  }
  .person { text-align: right; }
  .person-name {
    font-family: "Raleway", sans-serif; font-weight: 600;
    font-size: 30px; color: var(--lime-soft); line-height: 1.05;
  }
  .person-title {
    font-family: "Raleway", sans-serif; font-weight: 400;
    font-size: 18px; color: var(--text-white);
  }
  .divider { width: 1.5px; height: 72px; background: var(--mint); }
  .contacts { list-style: none; }
  .contact {
    display: flex; align-items: center; gap: 10px;
    font-family: "Raleway", sans-serif; font-weight: 400;
    font-size: 15px; color: var(--text-soft); line-height: 1.65;
  }
  .contact svg { width: 14px; height: 14px; flex: none; }
</style>
</head>
<body>
<div class="stage">
  <section class="card card-front">
    <div class="brand-front">
      <span class="brand-dot"></span>
      <span class="brand-name">VERODEX</span>
    </div>
    <span class="eco-band"></span>
  </section>

  <section class="card card-back">
    <span class="brand-corner">VERODEX</span>
    <div class="identity">
      <div class="person">
        <p class="person-name">MARCUS HALE</p>
        <p class="person-title">Founder &amp; CEO</p>
      </div>
      <span class="divider"></span>
      <ul class="contacts">
        <li class="contact">
          <svg viewBox="0 0 16 16" aria-hidden="true"><path fill="#67d7c9" d="M4 1.5l2.2 2.8-1.3 1.6a8 8 0 0 0 5.2 5.2l1.6-1.3 2.8 2.2-1.4 2.3C7.5 14.3 1.7 8.5 1.7 2.9z"/></svg>
          (555) 218-4093
        </li>
        <li class="contact">
          <svg viewBox="0 0 16 16" aria-hidden="true"><rect x="1" y="3" width="14" height="10" fill="#67d7c9"/><path d="M1 3l7 6 7-6" fill="none" stroke="#0054aa" stroke-width="1.3"/></svg>
          office@verodex.com
        </li>
        <li class="contact">
          <svg viewBox="0 0 16 16" aria-hidden="true"><circle cx="8" cy="8" r="6.5" fill="none" stroke="#67d7c9" stroke-width="1.6"/><path d="M1.5 8h13M8 1.5c-3 3.5-3 9.5 0 13M8 1.5c3 3.5 3 9.5 0 13" fill="none" stroke="#67d7c9" stroke-width="1.1"/></svg>
          verodex.com
        </li>
      </ul>
    </div>
    <span class="eco-band"></span>
  </section>
</div>
</body>
</html>
```